Business card design for my company.
I would like the card's background colour to be black. You can also see our web site to get an idea of our brand. https://www.tmwhomecrafting.com.au/
- Name
- Email

```html
<!DOCTYPE html>
<html lang="en">
<head>
<meta charset="utf-8">
<title>TMW Home Crafting – Business Card</title>
<link rel="stylesheet" href="https://fonts.googleapis.com/css2?family=Roboto:wght@400;500;700&display=swap">
<style>
  :root {
    --page-bg: #f2f2f2;
    --card-bg: #212125;
    --brand-green: #17974a;
    --text-light: #f4f4f6;
    --shadow: rgba(0, 0, 0, 0.22);
  }
  * { box-sizing: border-box; margin: 0; padding: 0; }
  html, body {
    width: 1200px;
    height: 987px;
    overflow: hidden;
    background: var(--page-bg);
    font-family: "Roboto", Arial, sans-serif;
    color: var(--text-light);
  }
  .canvas { position: relative; width: 1200px; height: 987px; }

  .card {
    position: absolute;
    left: 246px;
    width: 709px;
    height: 405px;
    background: var(--card-bg);
    border-radius: 34px;
    border-left: 5px solid var(--brand-green);
    border-bottom: 4px solid var(--brand-green);
    box-shadow: 0 10px 22px var(--shadow);
    overflow: hidden;
  }
  .card--front { top: 68px; }
  .card--back { top: 514px; }

  .brand {
    position: absolute;
    left: 0; right: 0;
    top: 170px;
    display: flex;
    justify-content: center;
    align-items: center;
    gap: 14px;
  }
  .brand__mark {
    width: 22px; height: 22px;
    background: var(--brand-green);
  }
  .brand__name {
    font-size: 42px;
    font-weight: 700;
    color: var(--text-light);
    letter-spacing: 0.5px;
  }

  .person {
    position: absolute;
    right: 30px;
    top: 176px;
    text-align: right;
  }
  .person__name {
    font-size: 38px;
    font-weight: 400;
    line-height: 1;
    color: var(--text-light);
  }
  .person__first { color: var(--brand-green); font-weight: 700; }
  .person__title {
    margin-top: 5px;
    font-size: 18px;
    letter-spacing: 0.6px;
  }
  .accent-bar {
    position: absolute;
    right: 0;
    top: 183px;
    width: 21px;
    height: 50px;
    background: var(--brand-green);
  }

  .contacts {
    position: absolute;
    right: 27px;
    top: 281px;
    list-style: none;
  }
  .contacts__item {
    display: flex;
    justify-content: flex-end;
    align-items: center;
    gap: 11px;
    height: 24px;
    font-size: 18.5px;
    letter-spacing: 0.5px;
  }
  .contacts__hl { color: var(--brand-green); }
  .contacts__icon { width: 16px; height: 16px; flex: none; }
</style>
</head>
<body>
<div class="canvas">

  <section class="card card--front">
    <div class="brand">
      <span class="brand__mark"></span>
      <span class="brand__name">TMW Home Crafting</span>
    </div>
  </section>

  <section class="card card--back">
    <div class="person">
      <p class="person__name"><span class="person__first">Liam</span> Porter</p>
      <p class="person__title">General Manager</p>
    </div>
    <div class="accent-bar"></div>

    <ul class="contacts">
      <li class="contacts__item">
        <span>0400 123 456</span>
        <svg class="contacts__icon" viewBox="0 0 24 24" fill="none" stroke="#17974a" stroke-width="2.4" stroke-linecap="round" stroke-linejoin="round"><path d="M5 3h4l2 5-3 2a11 11 0 0 0 6 6l2-3 5 2v4a2 2 0 0 1-2 2A17 17 0 0 1 3 5a2 2 0 0 1 2-2z"/></svg>
      </li>
      <li class="contacts__item">
        <span>www.<span class="contacts__hl">tmwhomecrafting</span>.com.au</span>
        <svg class="contacts__icon" viewBox="0 0 24 24" fill="none" stroke="#17974a" stroke-width="2.2"><circle cx="12" cy="12" r="10"/><path d="M2 12h20M12 2a15 15 0 0 1 0 20M12 2a15 15 0 0 0 0 20"/></svg>
      </li>
      <li class="contacts__item">
        <span>info@<span class="contacts__hl">tmwhomecrafting</span>.com.au</span>
        <svg class="contacts__icon" viewBox="0 0 24 24" fill="none" stroke="#17974a" stroke-width="2.2" stroke-linejoin="round"><rect x="2" y="5" width="20" height="14" rx="1"/><path d="M2 6l10 7 10-7"/></svg>
      </li>
      <li class="contacts__item">
        <span>Geelong, Victoria, Australia</span>
        <svg class="contacts__icon" viewBox="0 0 24 24" fill="none" stroke="#17974a" stroke-width="2.2"><path d="M12 22s-7-7-7-12a7 7 0 0 1 14 0c0 5-7 12-7 12z"/><circle cx="12" cy="10" r="2.5"/></svg>
      </li>
    </ul>
  </section>

</div>
</body>
</html>
```